Retail Jewelry Business Card Design Project

We are in need of a new business card design for a retail jewelry store. This store is in the business of fine jewelry including but not specific to bridal jewelry, diamonds, designer jewelry and watches.

This store has been in business for 20 years but continues to strive for a modern professional appeal. The main colors use for this business are a royal blue, white and silver.

Target Market(s)

Target market is ages 18-50

Industry/Entity Type

Jewelry

Requirements
Must have
• Sales Person Name
Sales Person Email Address

Store Address
Store Phone
Website

Standard business card size. No odd shapes or sizes.
Nice to have
• Overall modern feel for card.

We have thought that a design with a nice feature of the logo on the back of the card would be nice but open to ideas.
Should not have
• No specific images of jewelry should be used.

```html
<!DOCTYPE html>
<html lang="en">
<head>
<meta charset="utf-8">
<title>Hollis Grant Fine Jewelry – Business Cards</title>
<link rel="stylesheet" href="https://fonts.googleapis.com/css2?family=Tinos:ital,wght@0,400;0,700;1,700&family=Arimo:wght@400&display=swap">
<style>
  :root {
    --royal-blue: #2e3192;
    --royal-blue-ink: #2b2f8f;
    --silver: #e6e7ec;
    --white: #ffffff;
    --text-grey: #4a4a4a;
    --rule-grey: #c9c9cf;
    --backdrop: #ecebe8;
  }
  * { margin: 0; padding: 0; box-sizing: border-box; }
  html, body {
    width: 1200px;
    height: 804px;
    overflow: hidden;
    background: var(--backdrop);
  }
  .stage {
    position: relative;
    width: 1200px;
    height: 804px;
  }
  .card {
    position: absolute;
    width: 620px;
    height: 354px;
    border-radius: 4px;
    box-shadow: 0 2px 10px rgba(0,0,0,0.18);
  }
  .card-front {
    left: 60px;
    top: 70px;
    background: var(--white);
  }
  .card-back {
    left: 520px;
    top: 380px;
    background: var(--royal-blue);
  }
  .brand-name {
    position: absolute;
    left: 0;
    right: 0;
    text-align: center;
    font-family: "Tinos", serif;
    font-weight: 700;
    letter-spacing: 0.04em;
    line-height: 1.1;
  }
  .card-front .brand-name {
    top: 36px;
    font-size: 44px;
    color: var(--royal-blue-ink);
  }
  .card-back .brand-name {
    top: 96px;
    font-size: 50px;
    color: var(--silver);
  }
  .brand-name .brand-line {
    display: block;
  }
  .brand-name .brand-line-small {
    font-size: 0.6em;
    letter-spacing: 0.2em;
  }
  .contact-block {
    position: absolute;
    top: 190px;
    left: 0;
    right: 0;
    display: flex;
    justify-content: center;
  }
  .person {
    width: 262px;
    padding-right: 22px;
    padding-top: 72px;
    text-align: right;
    font-family: "Tinos", serif;
  }
  .person-name {
    font-style: italic;
    font-weight: 700;
    font-size: 18px;
    color: var(--royal-blue-ink);
    margin-bottom: 6px;
  }
  .person-address {
    font-size: 16px;
    line-height: 1.3;
    color: var(--text-grey);
  }
  .divider {
    width: 1px;
    height: 138px;
    background: var(--rule-grey);
  }
  .contact-list {
    list-style: none;
    width: 280px;
    padding-left: 16px;
    padding-top: 6px;
    font-family: "Tinos", serif;
    font-size: 16px;
    color: var(--text-grey);
  }
  .contact-list li {
    display: flex;
    align-items: center;
    gap: 8px;
    margin-bottom: 8px;
  }
  .contact-icon {
    width: 13px;
    height: 13px;
    flex: none;
  }
  .back-website {
    position: absolute;
    left: 0;
    right: 0;
    top: 262px;
    text-align: center;
    font-family: "Arimo", sans-serif;
    font-size: 17px;
    letter-spacing: 0.16em;
    color: var(--white);
  }
</style>
</head>
<body>
<main class="stage">

  <section class="card card-front" aria-label="Business card front">
    <h1 class="brand-name">
      <span class="brand-line">Hollis Grant</span>
      <span class="brand-line brand-line-small">FINE JEWELRY</span>
    </h1>

    <div class="contact-block">
      <div class="person">
        <p class="person-name">Hollis Grant Marlowe</p>
        <p class="person-address">2280 Ashford Lane<br>Bay Harbor, FL 32500</p>
      </div>
      <div class="divider"></div>
      <ul class="contact-list">
        <li>
          <svg class="contact-icon" viewBox="0 0 14 14" aria-hidden="true">
            <circle cx="7" cy="7" r="7" fill="var(--royal-blue)"/>
            <path d="M4.6 3.6 L5.8 3.4 L6.4 5.2 L5.6 5.8 C6 6.8 7 7.8 8 8.3 L8.6 7.5 L10.4 8.1 L10.2 9.3 C7 9.6 4.3 6.9 4.6 3.6 Z" fill="var(--white)"/>
          </svg>
          <span>555-014-2290</span>
        </li>
        <li>
          <svg class="contact-icon" viewBox="0 0 14 14" aria-hidden="true">
            <circle cx="7" cy="7" r="7" fill="var(--royal-blue)"/>
            <rect x="3.3" y="4.5" width="7.4" height="5" fill="var(--white)"/>
            <path d="M3.3 4.5 L7 7.4 L10.7 4.5" fill="none" stroke="var(--royal-blue)" stroke-width="0.8"/>
          </svg>
          <span>hollis@hollisgrantjewelry.com</span>
        </li>
        <li>
          <svg class="contact-icon" viewBox="0 0 14 14" aria-hidden="true">
            <circle cx="7" cy="7" r="7" fill="var(--royal-blue)"/>
            <circle cx="7" cy="7" r="4" fill="none" stroke="var(--white)" stroke-width="0.9"/>
            <ellipse cx="7" cy="7" rx="1.7" ry="4" fill="none" stroke="var(--white)" stroke-width="0.8"/>
            <line x1="3" y1="7" x2="11" y2="7" stroke="var(--white)" stroke-width="0.8"/>
          </svg>
          <span>www.hollisgrantjewelry.com</span>
        </li>
      </ul>
    </div>
  </section>

  <section class="card card-back" aria-label="Business card back">
    <h2 class="brand-name">
      <span class="brand-line">Hollis Grant</span>
      <span class="brand-line brand-line-small">FINE JEWELRY</span>
    </h2>
    <p class="back-website">www.hollisgrantjewelry.com</p>
  </section>

</main>
</body>
</html>
```